Sales presentation introduction for Finance and Tech firms

Our business is two fold - 1) recruitment 2) consultancy. We would like a one or two page template that we can use to send to potential clients. The template will ideally be the same for the recruitment and consultancy side. We need to be able to edit the template to enter text.

I have attached our logo so you can see what we currently use on Corvella.

Sector is financial services and technology. We do not intent to have lots of text but the layout/images/designs to be used should cover some of page in a way that it takes up some space to avoid having to write lot of text.

Open to colour suggestions.

Please look at the attached word doc to see the text I would like for the two presentations.

Happy to answer questions.

Target Market(s)

Directors

Industry/Entity Type

Finance and tech companies

Colors
0094D4
00A9DD
6FCCEA
C7EBF8
E9F6FB

Requirements
Must have
• Editable text

```html
<!DOCTYPE html>
<html lang="en">
<head>
<meta charset="utf-8">
<title>Halvern Advisory – Consultancy and Recruitment Flyers</title>
<link href="https://fonts.googleapis.com/css2?family=Barlow:wght@400;500;600;700&family=Barlow+Semi+Condensed:wght@700&display=swap" rel="stylesheet">
<style>
:root{
  --sheet:#707070;
  --paper:#ffffff;
  --blue:#1b7cc4;
  --blue-dark:#0b56a6;
  --blue-light:#5fb9e9;
  --title-blue:#14599f;
  --pale:#e5f3fb;
  --ink:#1d1d1b;
  --footer:#231f20;
}
*{margin:0;padding:0;box-sizing:border-box}
html,body{width:958px;height:1200px;overflow:hidden;background:var(--sheet)}
body{position:relative;font-family:"Barlow",Arial,sans-serif;color:var(--ink)}
.defs{position:absolute;width:0;height:0}
.flyer{position:absolute;width:678px;height:958px;background:var(--paper);overflow:hidden;transform:scale(.5567);transform-origin:0 0}
.flyer--tl{left:82.4px;top:58.4px}
.flyer--tr{left:492.6px;top:58.4px}
.flyer--bl{left:82.4px;top:623.5px}
.flyer--br{left:492.6px;top:623.5px}
.hero{position:absolute;left:0;top:0;width:678px;height:410px}
.brand{position:absolute;left:40px;top:94px;font-size:31px;font-weight:500;color:var(--ink)}
.tagline{position:absolute;left:40px;top:150px;white-space:nowrap;color:#fff;font-size:13px;font-weight:600;line-height:16.5px}
.heading{position:absolute;left:40px;top:222px;font-family:"Barlow Semi Condensed","Barlow",sans-serif;font-size:21px;font-weight:700;letter-spacing:.2px}
.intro{position:absolute;left:40px;top:252px;white-space:nowrap;font-size:11.6px;line-height:15.1px}
.intro--wide{top:341px}
.intro--spec{top:341px}
.intro strong{color:var(--title-blue);font-weight:600}
.services{position:absolute;left:40px;display:grid;grid-template-columns:220px 227px 200px;grid-auto-rows:74px}
.services--consult{top:411px}
.services--recruit{top:655px}
.service{display:flex;align-items:center;gap:17px;font-size:13.5px;line-height:16.5px}
.service svg{width:61px;height:61px;flex:none}
.expertise{position:absolute;left:0;top:635px;width:678px;height:277px;background:var(--pale)}
.area{position:absolute;width:290px}
.area svg{position:absolute;left:0;top:0;width:60px;height:60px}
.area h3{margin-left:71px;font-size:15px;font-weight:700;color:var(--title-blue);line-height:18px}
.area p{margin-left:71px;font-size:9px;line-height:12.3px;text-align:justify;width:210px}
.footer{position:absolute;left:0;top:912px;width:678px;height:46px;background:var(--footer);color:#fff;font-size:15px}
.contact{position:absolute;top:12px;display:flex;align-items:center;gap:8px;letter-spacing:.3px}
.contact svg{width:22px;height:22px}
.columns{position:absolute;left:40px;top:408px;width:600px;font-size:10px;line-height:13px}
.col-left{position:absolute;left:0;top:0;width:280px;font-weight:500;text-align:justify}
.col-right{position:absolute;left:312px;top:0;width:285px;font-weight:500;text-align:justify}
.ticks{list-style:none;margin-top:12px}
.ticks li{position:relative;padding-left:13px;margin-bottom:7.6px}
.ticks li::before{content:"";position:absolute;left:0;top:3px;width:7px;height:7px;border-radius:50%;background:var(--blue)}
.tick-grid{list-style:none;display:grid;grid-template-columns:145px 130px;column-gap:18px;row-gap:12px;margin-top:10px;font-size:9.4px;line-height:12px;text-align:left}
.tick-grid li{position:relative;padding-left:13px;min-height:52px}
.tick-grid li::before{content:"";position:absolute;left:0;top:3px;width:7px;height:7px;border-radius:50%;background:var(--blue)}
.closing{position:absolute;left:40px;top:598px;width:600px;font-size:10px;line-height:13px;font-weight:500}
</style>
</head>
<body>

<svg class="defs" aria-hidden="true">
  <defs>
    <symbol id="service-icon" viewBox="0 0 60 60">
      <circle cx="30" cy="30" r="30" fill="#1b7cc4"/>
      <circle cx="30" cy="30" r="25" fill="none" stroke="#fff" stroke-width="1.6"/>
      <rect x="20" y="17" width="20" height="26" rx="2" fill="none" stroke="#fff" stroke-width="1.8"/>
      <line x1="24" y1="24" x2="36" y2="24" stroke="#fff" stroke-width="1.6"/>
      <line x1="24" y1="30" x2="36" y2="30" stroke="#fff" stroke-width="1.6"/>
      <line x1="24" y1="36" x2="32" y2="36" stroke="#fff" stroke-width="1.6"/>
    </symbol>
    <symbol id="area-icon" viewBox="0 0 60 60">
      <circle cx="30" cy="28" r="16" fill="none" stroke="#14599f" stroke-width="2.4"/>
      <rect x="22" y="22" width="16" height="12" rx="1.5" fill="none" stroke="#14599f" stroke-width="2.2"/>
      <line x1="6" y1="54" x2="54" y2="54" stroke="#14599f" stroke-width="2.4"/>
      <line x1="30" y1="44" x2="30" y2="54" stroke="#14599f" stroke-width="2.2"/>
    </symbol>
    <symbol id="phone-icon" viewBox="0 0 22 22">
      <circle cx="11" cy="11" r="10" fill="none" stroke="#fff" stroke-width="1.4"/>
      <path d="M7.5 6.5c-.8.8-.6 3 1.6 5.6s4.8 3.4 5.6 2.6l.9-.9-2-1.8-1.1.8c-.9-.4-2.4-1.9-2.8-2.8l.8-1.1-1.8-2z" fill="#fff"/>
    </symbol>
    <symbol id="mail-icon" viewBox="0 0 22 22">
      <circle cx="11" cy="11" r="10" fill="none" stroke="#fff" stroke-width="1.4"/>
      <rect x="6" y="7.5" width="10" height="7" fill="none" stroke="#fff" stroke-width="1.3"/>
      <path d="M6 7.5l5 4 5-4" fill="none" stroke="#fff" stroke-width="1.3"/>
    </symbol>
    <symbol id="web-icon" viewBox="0 0 22 22">
      <circle cx="11" cy="11" r="10" fill="none" stroke="#fff" stroke-width="1.4"/>
      <circle cx="11" cy="11" r="5.5" fill="none" stroke="#fff" stroke-width="1.2"/>
      <ellipse cx="11" cy="11" rx="2.3" ry="5.5" fill="none" stroke="#fff" stroke-width="1.1"/>
      <line x1="5.5" y1="11" x2="16.5" y2="11" stroke="#fff" stroke-width="1.1"/>
    </symbol>
    <linearGradient id="city-tone" x1="0" y1="0" x2="1" y2="1">
      <stop offset="0" stop-color="#3d6fa6"/>
      <stop offset=".5" stop-color="#9fc1e0"/>
      <stop offset="1" stop-color="#dbe9f5"/>
    </linearGradient>
    <radialGradient id="tech-tone" cx=".85" cy=".4" r=".8">
      <stop offset="0" stop-color="#8fd3f5"/>
      <stop offset=".25" stop-color="#2c6a9c"/>
      <stop offset="1" stop-color="#0b1a2e"/>
    </radialGradient>
  </defs>
</svg>

<!-- Consultancy · city -->
<section class="flyer flyer--tl">
  <svg class="hero" viewBox="0 0 678 410">
    <polygon points="0,139 428,139 475,208 0,208" fill="var(--blue)"/>
    <polygon points="318,0 678,0 678,265 648,395" fill="url(#city-tone)" role="img" aria-label="Photograph of glass office towers seen from below against a pale sky"/>
    <polygon points="300,0 318,0 648,382 645,398" fill="var(--blue-dark)"/>
    <polygon points="678,330 678,352 650,398 640,398" fill="var(--blue-dark)"/>
    <polygon points="678,372 678,400 660,400" fill="var(--blue-light)"/>
  </svg>
  <div class="brand">Halvern Advisory</div>
  <p class="tagline">A partner who brings new and innovative ideas to the table,<br>through extensive industry experience and knowledge.<br>Halvern will ensure you are prepared for growth.</p>
  <h2 class="heading">HALVERN CONSULTANCY</h2>
  <p class="intro">Halvern Advisory is a bespoke consultancy firm that specialises in buy side<br>investment. Through an industry based consultative approach we assist our<br>clients in preparing for, and facilitating, long term growth. Working closely with<br>our clients we combine innovative thinking and breakthrough technologies to<br>accelerate progress and, together, achieve enduring results.</p>
  <p class="intro intro--wide">Experienced in successfully delivering change for global organisations as well as assisting<br>smaller firms during their growth phase. Halvern will work with you create a workable model<br>and ensure successful delivery of the project.</p>
  <div class="services services--consult">
    <div class="service"><svg><use href="#service-icon"/></svg><span>Order<br>Management<br>and Trading</span></div>
    <div class="service"><svg><use href="#service-icon"/></svg><span>CRM/ Onboarding</span></div>
    <div class="service"><svg><use href="#service-icon"/></svg><span>Compliance</span></div>
    <div class="service"><svg><use href="#service-icon"/></svg><span>Investment<br>and<br>Research</span></div>
    <div class="service"><svg><use href="#service-icon"/></svg><span>Performance,<br>Risk and<br>Attribution</span></div>
    <div class="service"><svg><use href="#service-icon"/></svg><span>Finance<br>and<br>Accounting</span></div>
    <div class="service"><svg><use href="#service-icon"/></svg><span>Investment<br>and<br>Research</span></div>
    <div class="service"><svg><use href="#service-icon"/></svg><span>Client and<br>Regulatory<br>Reporting</span></div>
    <div class="service"><svg><use href="#service-icon"/></svg><span>Middle<br>and<br>Back Office</span></div>
  </div>
  <div class="expertise">
    <div class="area" style="left:40px;top:15px"><svg><use href="#area-icon"/></svg><h3>Business Strategy</h3><p>Halvern will help you create a business strategy tailored to your requirements. Ensuring each business process is defined and taken into account allows for a successful design. Creating and implementing an operating model that takes into account budget, resources, culture and your company's vision.</p></div>
    <div class="area" style="left:356px;top:15px"><svg><use href="#area-icon"/></svg><h3>Change management</h3><p>Halvern works with clients to deliver bespoke change initiatives. Rigorous business analysis and risk management allows for successful change initiatives. We work with you throughout the complete process, to ensure that delivery is based on value. Transition phases are challenging aspects of change initiatives which is why our team manage all transitions and the risk they carry.</p></div>
    <div class="area" style="left:40px;top:168px"><svg><use href="#area-icon"/></svg><h3>IT transformation</h3><p>Halvern is widely experienced in a range of technologies. We help with the implementation of software provider or design and develop bespoke services. Covering front to back office the team specialises in full project lifecycle from feasibility through to implementation.</p></div>
    <div class="area" style="left:356px;top:168px"><svg><use href="#area-icon"/></svg><h3>Organisational structure</h3><p>Halvern works with clients to improve resource capability and strategic partnerships. Acting as an extension of the HR function, we analyse business processes and ensure that our clients have the ability to manage changing workforce demands.</p></div>
  </div>
  <footer class="footer">
    <span class="contact" style="left:40px"><svg><use href="#phone-icon"/></svg>+44 (0) 7700 900123</span>
    <span class="contact" style="left:240px"><svg><use href="#mail-icon"/></svg>info@halvern.co.uk</span>
    <span class="contact" style="left:450px"><svg><use href="#web-icon"/></svg>www.halvern.co.uk</span>
  </footer>
</section>

<!-- Consultancy · tech -->
<section class="flyer flyer--tr">
  <svg class="hero" viewBox="0 0 678 410">
    <polygon points="0,139 428,139 475,208 0,208" fill="var(--blue)"/>
    <polygon points="318,0 678,0 678,265 632,362" fill="url(#tech-tone)" role="img" aria-label="Digital network graphic with connected icons around a glowing sphere on dark blue"/>
    <polygon points="300,0 318,0 632,375 628,395" fill="var(--blue-dark)"/>
    <polygon points="678,330 678,352 636,398 626,398" fill="var(--blue-dark)"/>
    <polygon points="678,372 678,400 652,400" fill="var(--blue-light)"/>
  </svg>
  <div class="brand">Halvern Advisory</div>
  <p class="tagline">A partner who brings new and innovative ideas to the table,<br>through extensive industry experience and knowledge.<br>Halvern will ensure you are prepared for growth.</p>
  <h2 class="heading">HALVERN CONSULTANCY</h2>
  <p class="intro">Halvern Advisory is a bespoke consultancy firm that specialises in buy side<br>investment. Through an industry based consultative approach we assist our<br>clients in preparing for, and facilitating, long term growth. Working closely with<br>our clients we combine innovative thinking and breakthrough technologies to<br>accelerate progress and, together, achieve enduring results.</p>
  <p class="intro intro--wide">Experienced in successfully delivering change for global organisations as well as assisting<br>smaller firms during their growth phase. Halvern will work with you create a workable model<br>and ensure successful delivery of the project.</p>
  <div class="services services--consult">
    <div class="service"><svg><use href="#service-icon"/></svg><span>Order<br>Management<br>and Trading</span></div>
    <div class="service"><svg><use href="#service-icon"/></svg><span>CRM/ Onboarding</span></div>
    <div class="service"><svg><use href="#service-icon"/></svg><span>Compliance</span></div>
    <div class="service"><svg><use href="#service-icon"/></svg><span>Investment<br>and<br>Research</span></div>
    <div class="service"><svg><use href="#service-icon"/></svg><span>Performance,<br>Risk and<br>Attribution</span></div>
    <div class="service"><svg><use href="#service-icon"/></svg><span>Finance<br>and<br>Accounting</span></div>
    <div class="service"><svg><use href="#service-icon"/></svg><span>Investment<br>and<br>Research</span></div>
    <div class="service"><svg><use href="#service-icon"/></svg><span>Client and<br>Regulatory<br>Reporting</span></div>
    <div class="service"><svg><use href="#service-icon"/></svg><span>Middle<br>and<br>Back Office</span></div>
  </div>
  <div class="expertise">
    <div class="area" style="left:40px;top:15px"><svg><use href="#area-icon"/></svg><h3>Business Strategy</h3><p>Halvern will help you create a business strategy tailored to your requirements. Ensuring each business process is defined and taken into account allows for a successful design. Creating and implementing an operating model that takes into account budget, resources, culture and your company's vision.</p></div>
    <div class="area" style="left:356px;top:15px"><svg><use href="#area-icon"/></svg><h3>Change management</h3><p>Halvern works with clients to deliver bespoke change initiatives. Rigorous business analysis and risk management allows for successful change initiatives. We work with you throughout the complete process, to ensure that delivery is based on value. Transition phases are challenging aspects of change initiatives which is why our team manage all transitions and the risk they carry.</p></div>
    <div class="area" style="left:40px;top:168px"><svg><use href="#area-icon"/></svg><h3>IT transformation</h3><p>Halvern is widely experienced in a range of technologies. We help with the implementation of software provider or design and develop bespoke services. Covering front to back office the team specialises in full project lifecycle from feasibility through to implementation.</p></div>
    <div class="area" style="left:356px;top:168px"><svg><use href="#area-icon"/></svg><h3>Organisational structure</h3><p>Halvern works with clients to improve resource capability and strategic partnerships. Acting as an extension of the HR function, we analyse business processes and ensure that our clients have the ability to manage changing workforce demands.</p></div>
  </div>
  <footer class="footer">
    <span class="contact" style="left:40px"><svg><use href="#phone-icon"/></svg>+44 (0) 7700 900123</span>
    <span class="contact" style="left:240px"><svg><use href="#mail-icon"/></svg>info@halvern.co.uk</span>
    <span class="contact" style="left:450px"><svg><use href="#web-icon"/></svg>www.halvern.co.uk</span>
  </footer>
</section>

<!-- Recruitment · city -->
<section class="flyer flyer--bl">
  <svg class="hero" viewBox="0 0 678 410">
    <polygon points="0,139 428,139 475,208 0,208" fill="var(--blue)"/>
    <polygon points="318,0 678,0 678,265 648,395" fill="url(#city-tone)" role="img" aria-label="Photograph of glass office towers seen from below against a pale sky"/>
    <polygon points="300,0 318,0 648,382 645,398" fill="var(--blue-dark)"/>
    <polygon points="678,330 678,352 650,398 640,398" fill="var(--blue-dark)"/>
    <polygon points="678,372 678,400 660,400" fill="var(--blue-light)"/>
  </svg>
  <div class="brand">Halvern Advisory</div>
  <p class="tagline">A partner who brings new and innovative ideas to the table,<br>through extensive industry experience and knowledge.<br>Halvern will ensure you are prepared for growth.</p>
  <h2 class="heading">HALVERN RECRUITMENT</h2>
  <p class="intro">Halvern is more than an ordinary recruitment service. Our experts work with<br>clients to develop a HR strategy that maps current, and impending, organisational<br>needs; using research to effectively benchmark. We are developing various talent<br>communities that provide effective, and timely, recruitment solutions for our clients.</p>
  <p class="intro intro--spec"><strong>Specialists in:</strong> Asset Management recruitment with a specialisation in I.T, Operations,<br>Regulation and Change Management.</p>
  <div class="columns">
    <div class="col-left">Halvern acts as an extension of your HR function, providing an end-to-end permanent and contingent talent acquisition solution, taking full accountability and ownership for the entire recruitment process, which includes:
      <ul class="ticks"><li>Workforce Planning</li><li>Strategic Sourcing</li><li>Talent Engagement</li><li>Candidate Management</li><li>Weekly vacancy updates</li></ul>
    </div>
    <div class="col-right">We recognise that hiring can be a lengthy process, therefore we partner with you to ensure you only interview top quantile candidates, cutting out multiple meetings with multiple candidates. Giving hiring managers time back in their diaries to do their day jobs and reducing the time to hire. This is achieved by:
      <ul class="tick-grid"><li>Understanding the roles, and partnering with you to build meaningful job descriptions</li><li>Support with interviews and we ensure the candidate has a positive experience</li><li>Candidates are fully screened and interviewed prior to presentation to you</li><li>Qualified shortlist of top 3 candidates</li></ul>
    </div>
  </div>
  <p class="closing">Halvern recruitment partners with principal business consultants from Halvern consultancy to ensure candidates are properly screened before presenting to our clients. This allows for our clients to focus on only interviewing the best on the market.</p>
  <div class="services services--recruit">
    <div class="service"><svg><use href="#service-icon"/></svg><span>Order<br>Management<br>and Trading</span></div>
    <div class="service"><svg><use href="#service-icon"/></svg><span>CRM/ Onboarding</span></div>
    <div class="service"><svg><use href="#service-icon"/></svg><span>Compliance</span></div>
    <div class="service"><svg><use href="#service-icon"/></svg><span>Investment<br>and<br>Research</span></div>
    <div class="service"><svg><use href="#service-icon"/></svg><span>Performance,<br>Risk and<br>Attribution</span></div>
    <div class="service"><svg><use href="#service-icon"/></svg><span>Finance<br>and<br>Accounting</span></div>
    <div class="service"><svg><use href="#service-icon"/></svg><span>Investment<br>and<br>Research</span></div>
    <div class="service"><svg><use href="#service-icon"/></svg><span>Client and<br>Regulatory<br>Reporting</span></div>
    <div class="service"><svg><use href="#service-icon"/></svg><span>Middle<br>and<br>Back Office</span></div>
  </div>
  <footer class="footer">
    <span class="contact" style="left:40px"><svg><use href="#phone-icon"/></svg>+44 (0) 7700 900123</span>
    <span class="contact" style="left:240px"><svg><use href="#mail-icon"/></svg>info@halvern.co.uk</span>
    <span class="contact" style="left:450px"><svg><use href="#web-icon"/></svg>www.halvern.co.uk</span>
  </footer>
</section>

<!-- Recruitment · tech -->
<section class="flyer flyer--br">
  <svg class="hero" viewBox="0 0 678 410">
    <polygon points="0,139 428,139 475,208 0,208" fill="var(--blue)"/>
    <polygon points="318,0 678,0 678,265 632,362" fill="url(#tech-tone)" role="img" aria-label="Digital network graphic with connected icons around a glowing sphere on dark blue"/>
    <polygon points="300,0 318,0 632,375 628,395" fill="var(--blue-dark)"/>
    <polygon points="678,330 678,352 636,398 626,398" fill="var(--blue-dark)"/>
    <polygon points="678,372 678,400 652,400" fill="var(--blue-light)"/>
  </svg>
  <div class="brand">Halvern Advisory</div>
  <p class="tagline">A partner who brings new and innovative ideas to the table,<br>through extensive industry experience and knowledge.<br>Halvern will ensure you are prepared for growth.</p>
  <h2 class="heading">HALVERN RECRUITMENT</h2>
  <p class="intro">Halvern is more than an ordinary recruitment service. Our experts work with<br>clients to develop a HR strategy that maps current, and impending, organisational<br>needs; using research to effectively benchmark. We are developing various talent<br>communities that provide effective, and timely, recruitment solutions for our clients.</p>
  <p class="intro intro--spec"><strong>Specialists in:</strong> Asset Management recruitment with a specialisation in I.T, Operations,<br>Regulation and Change Management.</p>
  <div class="columns">
    <div class="col-left">Halvern acts as an extension of your HR function, providing an end-to-end permanent and contingent talent acquisition solution, taking full accountability and ownership for the entire recruitment process, which includes:
      <ul class="ticks"><li>Workforce Planning</li><li>Strategic Sourcing</li><li>Talent Engagement</li><li>Candidate Management</li><li>Weekly vacancy updates</li></ul>
    </div>
    <div class="col-right">We recognise that hiring can be a lengthy process, therefore we partner with you to ensure you only interview top quantile candidates, cutting out multiple meetings with multiple candidates. Giving hiring managers time back in their diaries to do their day jobs and reducing the time to hire. This is achieved by:
      <ul class="tick-grid"><li>Understanding the roles, and partnering with you to build meaningful job descriptions</li><li>Support with interviews and we ensure the candidate has a positive experience</li><li>Candidates are fully screened and interviewed prior to presentation to you</li><li>Qualified shortlist of top 3 candidates</li></ul>
    </div>
  </div>
  <p class="closing">Halvern recruitment partners with principal business consultants from Halvern consultancy to ensure candidates are properly screened before presenting to our clients. This allows for our clients to focus on only interviewing the best on the market.</p>
  <div class="services services--recruit">
    <div class="service"><svg><use href="#service-icon"/></svg><span>Order<br>Management<br>and Trading</span></div>
    <div class="service"><svg><use href="#service-icon"/></svg><span>CRM/ Onboarding</span></div>
    <div class="service"><svg><use href="#service-icon"/></svg><span>Compliance</span></div>
    <div class="service"><svg><use href="#service-icon"/></svg><span>Investment<br>and<br>Research</span></div>
    <div class="service"><svg><use href="#service-icon"/></svg><span>Performance,<br>Risk and<br>Attribution</span></div>
    <div class="service"><svg><use href="#service-icon"/></svg><span>Finance<br>and<br>Accounting</span></div>
    <div class="service"><svg><use href="#service-icon"/></svg><span>Investment<br>and<br>Research</span></div>
    <div class="service"><svg><use href="#service-icon"/></svg><span>Client and<br>Regulatory<br>Reporting</span></div>
    <div class="service"><svg><use href="#service-icon"/></svg><span>Middle<br>and<br>Back Office</span></div>
  </div>
  <footer class="footer">
    <span class="contact" style="left:40px"><svg><use href="#phone-icon"/></svg>+44 (0) 7700 900123</span>
    <span class="contact" style="left:240px"><svg><use href="#mail-icon"/></svg>info@halvern.co.uk</span>
    <span class="contact" style="left:450px"><svg><use href="#web-icon"/></svg>www.halvern.co.uk</span>
  </footer>
</section>

</body>
</html>
```